Beacon Advisory Website

I currently have a website www.beaconadvisoryinc.com. We are a IT Consulting Company. Our website will pretty much tell out our services. I am looking to enhance my website and make it look more professional. Looking for very classy and Contemporary look and design for my website.

It Company

```html
<!DOCTYPE html>
<html lang="en">
<head>
<meta charset="utf-8">
<title>Beacon Advisory</title>
<link href="https://fonts.googleapis.com/css2?family=Open+Sans:wght@400;600;700&display=swap" rel="stylesheet">
<style>
:root{
  --navy:#0d3d7a;
  --blue:#1a5fa8;
  --bright:#1f7ad0;
  --ink:#2f3a45;
  --muted:#6a7480;
  --soft:#eef1f4;
  --dark:#3a3d41;
  --white:#ffffff;
}
*{box-sizing:border-box;margin:0;padding:0}
html,body{width:1200px;height:2736px;overflow:hidden}
body{font-family:'Open Sans',sans-serif;color:var(--ink);background:var(--white)}
.topbar{height:30px;background:var(--navy);color:#cfe0f5;font-size:12px;display:flex;justify-content:flex-end;align-items:center;gap:34px;padding-right:44px}
.hero{position:relative;height:610px;background:linear-gradient(100deg,#eef3f8 0%,#e3eaf2 38%,#b9c3cf 60%,#4a5563 100%);overflow:hidden}
.hero-photo{position:absolute;right:0;top:0;width:700px;height:100%;background:linear-gradient(90deg,rgba(238,243,248,0) 0%,#9aa6b3 35%,#3b4756 100%)}
.header{position:absolute;top:10px;left:100px;right:100px;height:92px;background:rgba(255,255,255,.96);display:flex;align-items:center;justify-content:space-between;padding:0 20px 0 24px}
.brand{display:flex;align-items:center;gap:12px;font-weight:700;font-size:26px;color:var(--navy)}
.brand-mark{width:34px;height:34px;background:var(--bright)}
.nav{display:flex;gap:4px}
.nav a{font-size:12px;font-weight:600;color:var(--ink);text-decoration:none;padding:12px 16px;text-transform:uppercase}
.nav a.active{background:var(--navy);color:var(--white)}
.hero-copy{position:absolute;left:100px;top:200px}
.hero-copy h1{font-size:56px;font-weight:700;color:var(--navy);line-height:1.1}
.hero-copy h1 span{display:block;font-weight:400;color:var(--ink)}
.hero-copy p{margin-top:18px;font-size:24px;color:var(--bright)}
.btn-hero{display:inline-block;margin-top:44px;background:var(--bright);color:var(--white);font-size:18px;padding:14px 30px;border-radius:4px}
.section-title{text-align:center;font-size:44px;font-weight:600}
.divider{display:block;margin:18px auto 0}
.what{height:390px;padding-top:60px;text-align:center}
.what p{width:1000px;margin:34px auto 0;font-size:15px;line-height:1.7;color:var(--muted)}
.services{height:580px;background:linear-gradient(180deg,var(--blue),var(--navy));color:var(--white);padding-top:60px}
.services .section-title{color:var(--white)}
.service-row{display:flex;justify-content:center;gap:110px;margin-top:60px}
.service{width:250px;text-align:center}
.service-icon{width:108px;height:108px;border-radius:50%;border:3px solid rgba(255,255,255,.35);background:var(--bright);margin:0 auto;display:flex;align-items:center;justify-content:center}
.service h3{font-size:20px;font-weight:400;margin-top:26px}
.service p{font-size:14px;line-height:1.6;color:#cfe0f5;margin-top:14px}
.read{display:inline-block;margin-top:18px;font-size:13px;padding:6px 12px}
.read.boxed{border:1px solid var(--white)}
.testimonials{height:520px;padding-top:60px}
.quotes{display:flex;justify-content:center;gap:30px;margin-top:50px}
.quote{width:480px}
.quote-box{background:var(--soft);padding:28px 30px;font-size:14px;line-height:1.6;color:var(--muted);text-align:center}
.person{display:flex;align-items:center;gap:20px;margin:26px 0 0 26px}
.avatar{width:74px;height:74px;border-radius:50%;background:linear-gradient(135deg,#c9a58a,#6b5446)}
.person b{display:block;font-size:15px;font-weight:600}
.person span{font-size:13px;color:var(--muted)}
.contact{height:580px;background:var(--dark);color:var(--white);padding-top:50px}
.contact .section-title{color:var(--white)}
.contact-body{display:flex;gap:40px;margin:50px 0 0 100px}
.map{width:520px;height:300px;background:linear-gradient(135deg,#e8e4dc,#d8d3c8)}
.details h3{font-size:30px;font-weight:700}
.office-grid{display:grid;grid-template-columns:250px 250px;gap:26px 30px;margin-top:30px}
.office h4{font-size:18px;font-weight:600;margin-bottom:12px}
.line{display:flex;gap:12px;font-size:13px;line-height:1.5;color:#d6d9dd;margin-bottom:10px}
.pin{flex:none;width:30px;height:30px;border-radius:50%;background:var(--bright);display:flex;align-items:center;justify-content:center}
.footer{height:56px;background:var(--navy);color:#cfe0f5;font-size:13px;display:flex;align-items:center;justify-content:center}
</style>
</head>
<body>
<div class="topbar">
  <span>Meeting these demands for over 25 years</span>
  <span>Toll: 888-555-0147</span>
  <span>(555) 014-2290</span>
  <span>info@beaconadvisory.com</span>
</div>

<section class="hero">
  <div class="hero-photo" role="img" aria-label="Photo of two business professionals reviewing a tablet in an office"></div>
  <header class="header">
    <div class="brand"><span class="brand-mark"></span>Beacon Advisory</div>
    <nav class="nav">
      <a class="active">Home</a><a>Services</a><a>Solutions</a><a>Resources</a><a>Career</a><a>Contact Us</a>
    </nav>
  </header>
  <div class="hero-copy">
    <h1>Today's IT market<span>is a Dynamic</span></h1>
    <p>Meeting these demands for over 25 years</p>
    <span class="btn-hero">View More ›</span>
  </div>
</section>

<section class="what">
  <h2 class="section-title">What We Do</h2>
  <svg class="divider" width="24" height="20" viewBox="0 0 24 20"><path d="M2 2h20v12H9l-5 4v-4H2z" fill="#1f7ad0"/></svg>
  <p>Today's IT market is a dynamic, fast-paced industry, with ever-increasing demands. Meeting these demands for over 25 years, Beacon Advisory maintains a global presence, aggressively recruiting expertly qualified IT and Management Professionals from around the world and cultivating key partnerships with corporations to understand their business models and excel, with a goal of delivering exceptional client service and ensuring a consistent delivery of the talent needed to drive results.</p>
</section>

<section class="services">
  <h2 class="section-title">Our Services</h2>
  <svg class="divider" width="24" height="20" viewBox="0 0 24 20"><path d="M2 2h20v12H9l-5 4v-4H2z" fill="#ffffff"/></svg>
  <div class="service-row">
    <div class="service">
      <div class="service-icon"><svg width="44" height="36" viewBox="0 0 44 36"><rect x="2" y="2" width="40" height="26" rx="3" fill="none" stroke="#fff" stroke-width="3"/><path d="M14 34h16" stroke="#fff" stroke-width="3"/></svg></div>
      <h3>Consulting</h3>
      <p>Beacon Advisory has a seasoned team of professional consultants to work with you to help increase the business by providing IT services.</p>
      <span class="read">Read more »</span>
    </div>
    <div class="service">
      <div class="service-icon"><svg width="44" height="44" viewBox="0 0 44 44"><circle cx="22" cy="22" r="19" fill="none" stroke="#fff" stroke-width="3"/><circle cx="22" cy="17" r="6" fill="#fff"/><path d="M11 34c3-7 19-7 22 0" fill="#fff"/></svg></div>
      <h3>Staff Augmentation</h3>
      <p>For years Beacon Advisory has been offering our customers the ability to augment their existing staff.</p>
      <span class="read boxed">Read more »</span>
    </div>
    <div class="service">
      <div class="service-icon"><svg width="44" height="44" viewBox="0 0 44 44"><circle cx="22" cy="22" r="8" fill="none" stroke="#fff" stroke-width="3"/><circle cx="22" cy="22" r="17" fill="none" stroke="#fff" stroke-width="4" stroke-dasharray="6 5"/></svg></div>
      <h3>Offshore</h3>
      <p>For years Beacon Advisory has been offering our customers the ability to augment their existing staff.</p>
      <span class="read">Read more »</span>
    </div>
  </div>
</section>

<section class="testimonials">
  <h2 class="section-title">Testimonials</h2>
  <svg class="divider" width="24" height="20" viewBox="0 0 24 20"><path d="M2 2h20v12H9l-5 4v-4H2z" fill="#1f7ad0"/></svg>
  <div class="quotes">
    <div class="quote">
      <div class="quote-box">We have worked with their team on several projects and have found them reliable and responsive. The documentation is great and the final result is phenomenal.</div>
      <div class="person"><div class="avatar" role="img" aria-label="Portrait of Daniel Hart"></div><div><b>Daniel Hart</b><span>Business Company CEO</span></div></div>
    </div>
    <div class="quote">
      <div class="quote-box">We have worked with their team on several projects and have found them reliable and responsive. The documentation is great and the final result is phenomenal.</div>
      <div class="person"><div class="avatar" role="img" aria-label="Portrait of Laura Quinn"></div><div><b>Laura Quinn</b><span>Business Company CEO</span></div></div>
    </div>
  </div>
</section>

<section class="contact">
  <h2 class="section-title">Contact Us</h2>
  <svg class="divider" width="24" height="20" viewBox="0 0 24 20"><path d="M2 2h20v12H9l-5 4v-4H2z" fill="#ffffff"/></svg>
  <div class="contact-body">
    <div class="map" role="img" aria-label="Street map showing the head office location"></div>
    <div class="details">
      <h3>Beacon Advisory Inc.</h3>
      <div class="office-grid">
        <div class="office">
          <h4>Head Office</h4>
          <div class="line"><span class="pin"><svg width="12" height="16" viewBox="0 0 12 16"><path d="M6 0a6 6 0 0 1 6 6c0 4-6 10-6 10S0 10 0 6a6 6 0 0 1 6-6z" fill="#fff"/></svg></span><span>1420 Harbor Lane<br>Suite 210<br>Riverton, NJ 08077</span></div>
          <div class="line"><span class="pin"><svg width="14" height="14" viewBox="0 0 14 14"><path d="M3 0l3 3-2 2a8 8 0 0 0 5 5l2-2 3 3-2 3C6 14 0 8 0 3z" fill="#fff"/></svg></span><span>Phone: +1 (555) 014-2290</span></div>
        </div>
        <div class="office">
          <h4>West Coast Office</h4>
          <div class="line"><span class="pin"><svg width="12" height="16" viewBox="0 0 12 16"><path d="M6 0a6 6 0 0 1 6 6c0 4-6 10-6 10S0 10 0 6a6 6 0 0 1 6-6z" fill="#fff"/></svg></span><span>880 Bayview Road<br>Suite 300<br>Clearwater, FL 33755</span></div>
        </div>
        <div class="office">
          <h4>Technical Center</h4>
          <div class="line"><span class="pin"><svg width="12" height="16" viewBox="0 0 12 16"><path d="M6 0a6 6 0 0 1 6 6c0 4-6 10-6 10S0 10 0 6a6 6 0 0 1 6-6z" fill="#fff"/></svg></span><span>52 Mill Creek Drive<br>Suite 101<br>Hollis, NH 03049</span></div>
        </div>
      </div>
    </div>
  </div>
</section>

<footer class="footer">Copyright © 2007 - 2016 Beacon Advisory Ltd. All rights reserved.</footer>
</body>
</html>
```